BrivoTerna. Lantern of the Steady Harvest. Business card

Professional business card for BrivoTerna (Lantern of the Steady Harvest)
My rationale: Strategy-> Execution-> Results-> Value that lead to the BrivoTerna name: We put the Lantern of the Steady Harvest.
We deliver value to our customers helping them at defining a good strategy (cyan arrow). 90% of well formulated strategies fail due to poor execution so we also consider strategical execution very important (green arrow). Due to the execution we obtain the results (blue arrow). Finally, the results provide feedback to redefine strategy, and the new strategy has to be executed and new results obtained providing new feedback and on and on. It's like a wheel that finally, must create corporate value: value for shareholders, staholders, employees, providers...-

Target Market(s)

CEOs and steering comitees , invewrnent funds

Industry/Entity Type

Business Consultant

Contact Information for Business Card

Teodoro Vinsquel
CEO & Founder
teodoro.vinsquel@brivoterna-example.com
Mobile: +34 655.803.912
www.brivoterna-example.com

Colors

Designer to choose colors to be used in the design.

Requirements
Nice to have
• Nice to hace the words: Strategy, execution, results
• Nice to vave the claim: Lantern of the Steady Harvest
• The three colors should be shown:
• cyan for STRATEGY
• green for EXECUTION
• blue for RESULTS
Should not have
• Complete black background

```html
<!DOCTYPE html>
<html lang="en">
<head>
<meta charset="utf-8">
<title>BrivoTerna – Business Card</title>
<link href="https://fonts.googleapis.com/css2?family=Open+Sans:wght@400;600;700;800&display=swap" rel="stylesheet">
<style>
  :root {
    --page: #e7e4e1;
    --paper: #ffffff;
    --navy: #0a3192;
    --navy-deep: #08287a;
    --green: #8cc63f;
    --cyan: #2aa7df;
    --ink: #3a3a3a;
  }
  * { box-sizing: border-box; margin: 0; padding: 0; }
  html, body { width: 1200px; height: 997px; overflow: hidden; }
  body {
    background: var(--page);
    font-family: "Open Sans", Arial, sans-serif;
    position: relative;
  }
  .card {
    position: absolute;
    width: 560px;
    height: 320px;
    background: var(--paper);
    overflow: hidden;
    box-shadow: 0 6px 18px rgba(0,0,0,0.12);
  }
  /* Front: contact side */
  .card--front { left: 80px; top: 140px; }
  .front__panel {
    position: absolute; inset: 0;
    background: var(--navy);
    clip-path: polygon(45% 0, 100% 0, 100% 100%, 100% 100%);
  }
  .front__brand {
    position: absolute; left: 40px; top: 112px;
    font-weight: 800; font-size: 38px; letter-spacing: -0.5px;
    color: var(--navy);
  }
  .front__name-band {
    position: absolute; left: 270px; top: 138px; width: 290px; height: 34px;
    background: var(--navy-deep);
    clip-path: polygon(6% 0, 100% 0, 100% 100%, 0 100%);
    border-top: 1px solid rgba(255,255,255,0.35);
    color: #fff; font-weight: 700; font-size: 18px;
    display: flex; align-items: center; padding-left: 34px;
  }
  .front__title-band {
    position: absolute; left: 370px; top: 172px; width: 190px; height: 28px;
    background: var(--green);
    clip-path: polygon(8% 0, 100% 0, 100% 100%, 0 100%);
    color: #fff; font-weight: 600; font-size: 14px;
    display: flex; align-items: center; padding-left: 34px;
  }
  .front__contacts {
    position: absolute; left: 40px; top: 200px;
    list-style: none; font-size: 13.5px; color: var(--ink); line-height: 21px;
  }
  .front__contacts li { display: flex; align-items: center; gap: 8px; }
  .front__contacts svg { width: 12px; height: 12px; flex: none; }
  .front__pillars {
    position: absolute; left: 40px; top: 270px;
    font-size: 15px; color: var(--navy); word-spacing: 6px;
  }
  /* Back: brand side */
  .card--back { left: 560px; top: 520px; }
  .back__brand {
    position: absolute; left: 0; right: 0; top: 118px;
    text-align: center;
    font-weight: 800; font-size: 58px; letter-spacing: -1px;
    color: var(--navy);
  }
  .back__claim {
    position: absolute; left: 60px; right: 60px; top: 206px;
    display: flex; align-items: center; gap: 12px;
    font-size: 14px; color: var(--navy); white-space: nowrap;
  }
  .back__claim::before, .back__claim::after {
    content: ""; flex: 1; height: 1px; background: var(--cyan);
  }
</style>
</head>
<body>
  <section class="card card--front" aria-label="Business card, contact side">
    <div class="front__panel"></div>
    <div class="front__brand">BrivoTerna</div>
    <div class="front__name-band">Teodoro Vinsquel</div>
    <div class="front__title-band">CEO &amp; Founder</div>
    <ul class="front__contacts">
      <li>
        <svg viewBox="0 0 12 12" aria-hidden="true"><rect x="3" y="0.5" width="6" height="11" rx="1" fill="none" stroke="#0a3192" stroke-width="1.2"/><circle cx="6" cy="9.5" r="0.8" fill="#0a3192"/></svg>
        +34 655.803.912
      </li>
      <li>
        <svg viewBox="0 0 12 12" aria-hidden="true"><rect x="0.5" y="2.5" width="11" height="7" fill="#0a3192"/><path d="M0.5 2.5 L6 6.5 L11.5 2.5" fill="none" stroke="#fff" stroke-width="1"/></svg>
        teodoro.vinsquel@brivoterna-example.com
      </li>
      <li>
        <svg viewBox="0 0 12 12" aria-hidden="true"><circle cx="6" cy="6" r="5.2" fill="none" stroke="#0a3192" stroke-width="1.2"/><ellipse cx="6" cy="6" rx="2.2" ry="5.2" fill="none" stroke="#0a3192" stroke-width="1"/><line x1="0.8" y1="6" x2="11.2" y2="6" stroke="#0a3192" stroke-width="1"/></svg>
        www.brivoterna-example.com
      </li>
    </ul>
    <div class="front__pillars">Strategy - Execution - Results</div>
  </section>

  <section class="card card--back" aria-label="Business card, brand side">
    <div class="back__brand">BrivoTerna</div>
    <div class="back__claim">Lantern of the Steady Harvest</div>
  </section>
</body>
</html>
```